RTavenor Business Cards & Letterhead

I have a logo but need a design for some new business cards. We are a Design-Build Firm that specializes in the design and construction of commercial projects.
the cards need to be professional. no cartoon stuff.
i would like to have the cards in AI format so I can update the card as needed. Logo is provided.
Our Address is: 4187 Marlowe Ct. Larkfield, Eastbrook 27614

```html
<!DOCTYPE html>
<html lang="en">
<head>
<meta charset="utf-8">
<title>RTavenor Business Card</title>
<link rel="stylesheet" href="https://fonts.googleapis.com/css2?family=Arimo:ital,wght@0,400;0,700;1,400;1,700&display=swap">
<style>
  :root {
    --stage: #e4e4e6;
    --paper: #f3f3f3;
    --ink: #2a2a2a;
    --panel: #111111;
    --blue: #0b5fa8;
    --blue-deep: #08457e;
    --blue-light: #1a78c2;
    --white: #ffffff;
  }
  * { box-sizing: border-box; margin: 0; padding: 0; }
  html, body {
    width: 1200px; height: 1200px; overflow: hidden;
    background: var(--stage);
    font-family: "Arimo", Arial, sans-serif;
  }
  .canvas { position: relative; width: 1200px; height: 1200px; }

  .card {
    position: absolute;
    width: 760px; height: 434px;
    background: var(--paper);
    border-bottom: 4px solid var(--blue);
    border-right: 4px solid var(--blue);
    overflow: hidden;
  }
  .card--front { left: 110px; top: 140px; }
  .card--back  { left: 330px; top: 630px; }

  .wordmark {
    position: absolute;
    display: flex; align-items: center; gap: 10px;
    font-weight: 700; color: var(--ink); letter-spacing: 1px;
    white-space: nowrap;
  }
  .wordmark__square { background: var(--blue); display: block; flex: none; }
  .card--front .wordmark { left: 44px; top: 70px; font-size: 34px; }
  .card--front .wordmark__square { width: 24px; height: 24px; }

  .person { position: absolute; right: 62px; top: 62px; text-align: right; white-space: nowrap; }
  .person__name { font-weight: 700; font-style: italic; font-size: 30px; color: var(--blue); }
  .person__role { font-style: italic; font-size: 16px; color: var(--ink); margin-top: 4px; }

  .accent-block {
    position: absolute; left: 0; top: 172px; width: 262px; height: 262px;
    background: linear-gradient(135deg, var(--blue-light), var(--blue-deep));
    border-top-right-radius: 18px;
  }
  .info-panel {
    position: absolute; left: 282px; top: 172px; right: 0; bottom: 0;
    background: var(--panel);
    border-top-left-radius: 18px;
    padding: 46px 70px 0 0;
    color: var(--white);
    text-align: right;
  }
  .address { font-style: italic; font-size: 18px; line-height: 1.35; margin-bottom: 22px; white-space: nowrap; }
  .contact { list-style: none; font-style: italic; font-size: 18px; line-height: 1.45; }
  .contact li { display: flex; justify-content: flex-end; align-items: center; gap: 6px; white-space: nowrap; }
  .contact svg { width: 14px; height: 14px; fill: var(--blue-light); flex: none; }

  .card--back .wordmark {
    left: 0; right: 0; top: 180px; justify-content: center;
    font-size: 56px; letter-spacing: 2px;
  }
  .card--back .wordmark__square { width: 36px; height: 36px; }
  .corner-bar {
    position: absolute;
    background: linear-gradient(135deg, var(--blue-light), var(--blue-deep));
  }
  .corner-bar--top { right: 0; top: 0; width: 120px; height: 110px; border-bottom-left-radius: 18px; }
  .corner-bar--bottom-left { left: 0; bottom: 0; width: 90px; height: 120px; border-top-right-radius: 18px; }
  .corner-bar--bottom-right { right: 0; bottom: 0; width: 150px; height: 70px; }
</style>
</head>
<body>
<main class="canvas">

  <section class="card card--front" aria-label="Business card front">
    <div class="wordmark"><span class="wordmark__square"></span>RTAVENOR</div>
    <div class="person">
      <p class="person__name">Rowan Tavenor</p>
      <p class="person__role">CEO</p>
    </div>
    <div class="accent-block" role="img" aria-label="Blue brand decoration area"></div>
    <div class="info-panel">
      <p class="address">4187 Marlowe Ct. Larkfield,<br>Eastbrook 27614</p>
      <ul class="contact">
        <li>555.314.2876
          <svg viewBox="0 0 16 16"><path d="M4 1l3 3-2 2c1 2 3 4 5 5l2-2 3 3-2 3C7 14 2 9 1 3z"/></svg></li>
        <li>555.662.0418
          <svg viewBox="0 0 16 16"><path d="M4 0h8v16H4zM5.5 2v10h5V2z"/></svg></li>
        <li>rowan@rtavenor.com
          <svg viewBox="0 0 16 16"><path d="M0 3h16v10H0zM1 4l7 5 7-5z" fill-rule="evenodd"/></svg></li>
        <li>www.rtavenor.com
          <svg viewBox="0 0 16 16"><circle cx="8" cy="8" r="7"/><path d="M1 8h14M8 1v14" stroke="#111" stroke-width="1.2"/></svg></li>
      </ul>
    </div>
  </section>

  <section class="card card--back" aria-label="Business card back">
    <span class="corner-bar corner-bar--top"></span>
    <span class="corner-bar corner-bar--bottom-left"></span>
    <span class="corner-bar corner-bar--bottom-right"></span>
    <div class="wordmark"><span class="wordmark__square"></span>RTAVENOR</div>
  </section>

</main>
</body>
</html>
```